Yacht, Boats, Watersports company needs a redesign of business card

Hello Designers!
We are a Boat dealership company that sells fun in the water, we sell boats, Yachts, Kayaks and also yacht WaterSport toys. We are looking to redesign our business cards in to something a little bit more sophisticated. in a way that we can make better use of our company colors. I'm attaching a zipped file containing the company 3 sets of company logo which one is an horizontal another one is a vertical and also a chromed 3d logo. Also is included two set of business cards that we use and also some designs that i think it's interesting. We use PMS 2026c Orange and PMS 7687C Blue. I would like to see at least two different options with the orange as accent and also using blue as an accent color. It's really important for the business cards to have a font option and size that is legible to most people. Our current website is wwww.coralpennant.com. Please visit if you want to have a better feeling of the Boat dealership
You can send Single sided or double side options. We are now using single sided but we may be open for a double side option if we really like the design.
Target Market(s)
Marine, boat sales, yacht sales, water toys sales/
Contact Information for Business Card
Name: Dale Whitcombe
Address: 212 North Fenwick Lane,
Pelican Cove, FL 32917
Phone: 555-731-8842
Fax: 555:731-8843
Cell: 555-382-1490
Email: dw@coralpennant.com
Website: coralpennant.com
Requirements
Must have
- the current information of the business card provided.
logo
use the PMS Colors
Nice to have
- a touch of elegance and sophistication but simple
Should not have
- should not have any typography that is hard to read, the card should be simple but yet sophisticated.

```html
<!DOCTYPE html>
<html lang="en">
<head>
<meta charset="utf-8">
<title>Coral Pennant – Business Card</title>
<link rel="stylesheet" href="https://fonts.googleapis.com/css2?family=Michroma&family=Oswald:wght@600&family=Roboto:wght@400;500&display=swap">
<style>
  :root {
    --navy: #0f4476;
    --orange: #e95d2f;
    --paper: #f4f4f4;
    --ink: #2a2a2a;
    --backdrop: #e3e3e3;
  }
  * { margin: 0; padding: 0; box-sizing: border-box; }
  html, body { width: 1200px; height: 960px; overflow: hidden; }
  body { background: var(--backdrop); position: relative; font-family: "Roboto", Arial, sans-serif; }

  .card {
    position: absolute;
    left: 296px;
    width: 606px;
    height: 346px;
    overflow: hidden;
  }
  .card--front { top: 109px; background: var(--navy); }
  .card--back { top: 508px; background: var(--paper); }

  .card__ring { position: absolute; }
  .card--front .card__ring { left: -190px; top: -2px; width: 370px; height: 350px; }
  .card--back .card__ring { left: 438px; top: 0; width: 360px; height: 346px; }

  .wordmark {
    font-family: "Michroma", "Arial", sans-serif;
    text-transform: uppercase;
    white-space: nowrap;
  }
  .front__wordmark {
    position: absolute;
    left: 219px; top: 159px;
    font-size: 24px;
    letter-spacing: 2px;
    color: #ffffff;
  }
  .front__web {
    position: absolute;
    left: 298px; top: 294px;
    font-size: 16px;
    letter-spacing: 1.6px;
    color: var(--orange);
  }
  .front__web span { color: #ffffff; }

  .back__brand {
    position: absolute;
    left: 46px; top: 30px;
    width: 240px;
    text-align: center;
  }
  .brand__dot {
    display: block;
    width: 52px; height: 52px;
    margin: 0 auto 12px;
    border: 4px solid var(--orange);
    border-radius: 50%;
  }
  .back__wordmark { font-size: 16px; letter-spacing: 1.5px; color: var(--navy); }

  .back__name {
    position: absolute;
    left: 46px; top: 154px;
    font-family: "Oswald", "Arial Narrow", sans-serif;
    font-weight: 600;
    font-size: 22px;
    color: var(--navy);
    text-transform: uppercase;
  }
  .contact {
    position: absolute;
    left: 46px; top: 207px;
    list-style: none;
    font-size: 16px;
    color: var(--ink);
    line-height: 20px;
  }
  .contact li { display: flex; align-items: center; gap: 5px; }
  .contact svg { width: 14px; height: 14px; fill: var(--orange); flex: none; }
  .back__address {
    position: absolute;
    left: 46px; top: 295px;
    font-size: 16px;
    color: var(--ink);
  }
</style>
</head>
<body>

<section class="card card--front">
  <svg class="card__ring" viewBox="0 0 370 350" aria-hidden="true">
    <circle cx="185" cy="175" r="160" fill="none" stroke="var(--orange)" stroke-width="28"/>
  </svg>
  <p class="wordmark front__wordmark">Coral Pennant</p>
  <p class="front__web">coralpennant<span>.com</span></p>
</section>

<section class="card card--back">
  <svg class="card__ring" viewBox="0 0 360 346" aria-hidden="true">
    <circle cx="180" cy="173" r="155" fill="none" stroke="var(--orange)" stroke-width="28"/>
  </svg>

  <div class="back__brand">
    <span class="brand__dot"></span>
    <p class="wordmark back__wordmark">Coral Pennant</p>
  </div>

  <h1 class="back__name">Dale Whitcombe</h1>

  <ul class="contact">
    <li>
      <svg viewBox="0 0 24 24" aria-label="Phone"><path d="M6.6 10.8a15.2 15.2 0 0 0 6.6 6.6l2.2-2.2c.3-.3.7-.4 1-.2 1.1.4 2.3.6 3.6.6.6 0 1 .4 1 1V20c0 .6-.4 1-1 1A17 17 0 0 1 3 4c0-.6.4-1 1-1h3.5c.6 0 1 .4 1 1 0 1.3.2 2.5.6 3.6.1.3 0 .7-.2 1z"/></svg>
      555-731-8842
    </li>
    <li>
      <svg viewBox="0 0 24 24" aria-label="Fax"><path d="M7 3h10v4H7zM4 8h16a2 2 0 0 1 2 2v6h-4v5H6v-5H2v-6a2 2 0 0 1 2-2zm4 8v3h8v-3z"/></svg>
      555:731-8843
    </li>
    <li>
      <svg viewBox="0 0 24 24" aria-label="Mobile"><path d="M7 1h10a2 2 0 0 1 2 2v18a2 2 0 0 1-2 2H7a2 2 0 0 1-2-2V3a2 2 0 0 1 2-2zm0 3v14h10V4zm4 15.5v1.5h2v-1.5z"/></svg>
      555-382-1490
    </li>
    <li>
      <svg viewBox="0 0 24 24" aria-label="Email"><path d="M2 5h20v14H2zm2 2v.4l8 5.4 8-5.4V7zm0 2.8V17h16V9.8l-8 5.4z"/></svg>
      dw@coralpennant.com
    </li>
  </ul>

  <p class="back__address">212 North Fenwick Lane, Pelican Cove, FL 32917</p>
</section>

</body>
</html>
```